Bramwell Lodge Business Cards design with a logo

I want two Business cards designed with a very modern contemporary logo UNING 1920'S FONT STYLES with the following details

Address:
Bramwell Lodge
17 Pellham Road
Ardlowrie
G83 2RN

Details for card 1

Name: Dermot Ashby
email: Dermot.ashby@bramwell.lodge
Tel : +971 52 318 6094
Tel +44 7700 900 318

Details Card 2

Name: Dermot Ashby
email: Neville.osgood@bramwell.lodge
Tel : +971 52 430 9187

Bramwell lodge is a house that was built around 1880 and was used extensively in the 1920's for entertaining and parties in the arts scene, the house again will be resurrected to a modern entertainment venue

If you have any questions feel free to ask

Target Market(s)

The market for this is the young modern crowd

Industry/Entity Type

Entertainment Industry

Contact Information for Business Card

Address:
Bramwell Lodge
17 Pellham Road
Ardlowrie
G83 2RN

Details for card 1

Name: Dermot Ashby
Tel : +971 52 318 6094
Tel +44 7700 900 318

Details Card 2

Name: Neville Osgood
Tel : +971 52 430 9187

Logo Text

Bramwell Lodge

Font styles to use
Other font styles liked:
• 1920'S FONT STULES

Requirements
Must have
• Modern Contemporary, whilst taking into consideration the age of the house as detailed above. YOU MUT BE USING 1920'S FONT STYLES
Nice to have
• 1920'S FONT STYLES see attached image if a suggestion
Should not have
• Should not look old or dated

```html
<!DOCTYPE html>
<html lang="en">
<head>
<meta charset="utf-8">
<title>Bramwell Lodge Business Cards</title>
<link rel="stylesheet" href="https://fonts.googleapis.com/css2?family=Federo&display=swap">
<style>
  :root {
    --backdrop: #1c1c1d;
    --card: #232324;
    --card-deep: #151516;
    --pattern-glow: #2e2e30;
    --ink: #f4f4f4;
    --ink-soft: #cfcfcf;
    --rule: #bdbdbd;
  }
  * { box-sizing: border-box; margin: 0; padding: 0; }
  html, body {
    width: 1200px;
    height: 900px;
    overflow: hidden;
    background: var(--backdrop);
  }
  body {
    position: relative;
    font-family: "Federo", "Trebuchet MS", sans-serif;
    color: var(--ink);
    text-transform: uppercase;
  }
  .card {
    position: absolute;
    left: 250px;
    width: 700px;
    height: 400px;
    background: var(--card);
    overflow: hidden;
    box-shadow: 0 14px 30px rgba(0,0,0,0.55);
  }
  .card--front { top: 40px; }
  .card--back  { top: 470px; }

  .card__pattern {
    position: absolute;
    inset: 0;
    background:
      radial-gradient(ellipse at 50% 40%, var(--pattern-glow) 0%, transparent 70%),
      linear-gradient(160deg, var(--card) 0%, var(--card-deep) 100%);
  }

  /* Front */
  .brand {
    position: absolute;
    left: 0; right: 0;
    top: 110px;
    text-align: center;
  }
  .brand__mark {
    display: block;
    width: 58px;
    height: 58px;
    margin: 0 auto 26px;
    border: 2px solid var(--ink);
    border-radius: 50%;
  }
  .brand__name {
    font-size: 56px;
    font-weight: 400;
    letter-spacing: 2px;
    line-height: 1;
  }
  .brand__web {
    position: absolute;
    left: 0; right: 0;
    bottom: 46px;
    text-align: center;
    font-size: 21px;
    letter-spacing: 1px;
  }

  /* Back */
  .person {
    position: absolute;
    left: 40px;
    top: 140px;
    width: 260px;
    text-align: right;
  }
  .person__name { font-size: 30px; font-weight: 400; letter-spacing: 1px; line-height: 1.1; }
  .person__role { font-size: 14px; color: var(--ink-soft); margin-top: 6px; letter-spacing: 1px; }
  .divider {
    position: absolute;
    left: 320px;
    top: 128px;
    width: 1.5px;
    height: 96px;
    background: var(--rule);
  }
  .contacts {
    position: absolute;
    left: 340px;
    top: 132px;
    list-style: none;
    font-size: 17px;
    letter-spacing: 0.5px;
  }
  .contacts li {
    display: flex;
    align-items: center;
    gap: 10px;
    line-height: 22px;
    white-space: nowrap;
  }
  .contacts svg { width: 13px; height: 13px; flex: none; }
  .address {
    position: absolute;
    left: 40px;
    bottom: 52px;
    display: flex;
    align-items: center;
    gap: 12px;
    font-size: 17px;
    letter-spacing: 1px;
    white-space: nowrap;
  }
  .address__mark {
    width: 16px;
    height: 16px;
    background: var(--ink);
  }
</style>
</head>
<body>

  <section class="card card--front">
    <div class="card__pattern" role="img" aria-label="Art deco pattern of diamonds, dotted squares and fan lines in dark grey"></div>
    <div class="brand">
      <span class="brand__mark"></span>
      <h1 class="brand__name">Bramwell Lodge</h1>
    </div>
    <p class="brand__web">www.bramwelllodge.com</p>
  </section>

  <section class="card card--back">
    <div class="card__pattern" role="img" aria-label="Art deco pattern of diamonds, dotted squares and fan lines in dark grey"></div>

    <div class="person">
      <h2 class="person__name">Dermot Ashby</h2>
      <p class="person__role">Director</p>
    </div>
    <span class="divider"></span>

    <ul class="contacts">
      <li>
        <svg viewBox="0 0 16 16" aria-hidden="true"><path d="M4 1h3l1 4-2 1c1 2 2 3 4 4l1-2 4 1v3c0 1-1 2-2 2C7 14 2 9 2 3c0-1 1-2 2-2z" fill="#f4f4f4"/></svg>
        +971 52 318 6094
      </li>
      <li>
        <svg viewBox="0 0 16 16" aria-hidden="true"><path d="M1 6c0-2 14-2 14 0v1h-4V5H5v2H1z M4 8h8l2 6H2z" fill="#f4f4f4"/></svg>
        +44 7700 900 318
      </li>
      <li>
        <svg viewBox="0 0 16 16" aria-hidden="true"><rect x="1" y="3" width="14" height="10" fill="none" stroke="#f4f4f4" stroke-width="1.5"/><path d="M1 3l7 6 7-6" fill="none" stroke="#f4f4f4" stroke-width="1.5"/></svg>
        Dermot.ashby@bramwell.lodge
      </li>
      <li>
        <svg viewBox="0 0 16 16" aria-hidden="true"><circle cx="8" cy="8" r="6.5" fill="none" stroke="#f4f4f4" stroke-width="1.3"/><ellipse cx="8" cy="8" rx="3" ry="6.5" fill="none" stroke="#f4f4f4" stroke-width="1.1"/><path d="M1.5 8h13" stroke="#f4f4f4" stroke-width="1.1"/></svg>
        www.bramwelllodge.com
      </li>
    </ul>

    <p class="address">
      <span class="address__mark"></span>
      Bramwell Lodge, 17 Pellham Road Ardlowrie&nbsp;&nbsp;G83 2RN
    </p>
  </section>

</body>
</html>
```